Boutique personal training and fitness studio - banner ad design

We need a 'revolving' banner ad designed for our personal training and fitness studio. There are three separate offers (i.e. 3 pages to the advertisements)
Offer 1
PT Starter Pack
3 personal training sessions
$119
New clients only
Offer 2
Group fitness
2 weeks unlimited group fitness classes
$29
New clients only
Offer 3
Strength starter pack
2 weeks unlimited group fitness classes and 2 PT sessions
$89
New clients only
Please do not put the words "Offer 1, 2 or 3" in the ads - just the text following each offer.
Each advertisement should be sized to fit across around half of the webpage and be in landscape format.
Each advertisement should have a suitable picture (no cartoons) and should be complimentary to the existing website.
Each advertisement should also include the logo (attached)
www.larkvalepowerhouse.com.au

```html
<!DOCTYPE html>
<html lang="en">
<head>
<meta charset="utf-8">
<title>Larkvale Powerhouse – Group Fitness Offer</title>
<link rel="stylesheet" href="https://fonts.googleapis.com/css2?family=Gelasio:wght@400;700&display=swap">
<style>
  :root {
    --bg-dark: #1c1c1c;
    --bg-mid: #3a3a3a;
    --bg-glow: #5c5c5c;
    --text-light: #e6e6e6;
    --text-white: #ffffff;
    --accent-red: #d3151b;
    --accent-red-dark: #7a0a0d;
    --badge-silver: #c9c9c9;
    --photo-light: #d8d8d8;
    --photo-mid: #8a8a8a;
  }
  html, body {
    margin: 0;
    padding: 0;
    width: 1200px;
    height: 599px;
    overflow: hidden;
    background: var(--bg-dark);
  }
  .banner {
    position: relative;
    width: 1200px;
    height: 599px;
    overflow: hidden;
    font-family: "Gelasio", Georgia, serif;
    background:
      radial-gradient(ellipse 520px 380px at 900px 300px, var(--bg-glow) 0%, var(--bg-mid) 45%, transparent 80%),
      radial-gradient(ellipse 420px 320px at 300px 300px, #454545 0%, transparent 75%),
      var(--bg-dark);
  }
  .brand {
    position: absolute;
    left: 95px;
    top: 30px;
    width: 430px;
    height: 130px;
    display: flex;
    align-items: center;
    justify-content: center;
    gap: 18px;
  }
  .brand-dot {
    width: 26px;
    height: 26px;
    border-radius: 50%;
    background: var(--badge-silver);
    flex: none;
  }
  .brand-name {
    font-weight: 700;
    font-size: 44px;
    letter-spacing: 2px;
    text-transform: uppercase;
    color: var(--text-light);
    white-space: nowrap;
  }
  .offer {
    position: absolute;
    left: 10px;
    width: 630px;
    text-align: center;
    margin: 0;
    font-weight: 700;
    line-height: 1;
    white-space: nowrap;
  }
  .offer-title {
    top: 190px;
    font-size: 60px;
    color: var(--text-light);
    text-shadow: 0 2px 3px #000;
  }
  .offer-duration {
    top: 262px;
    font-size: 40px;
    color: var(--text-light);
  }
  .offer-headline {
    top: 298px;
    font-size: 122px;
    letter-spacing: -2px;
    color: var(--accent-red);
    text-shadow: 0 3px 0 var(--accent-red-dark), 0 5px 8px #000;
  }
  .offer-detail {
    top: 410px;
    font-size: 40px;
    font-weight: 400;
    color: var(--text-white);
  }
  .offer-price {
    top: 450px;
    font-size: 50px;
    color: var(--accent-red);
    text-shadow: 0 2px 3px #000;
  }
  .offer-eligibility {
    top: 520px;
    font-size: 62px;
    color: var(--text-light);
    text-shadow: 0 2px 3px #000;
  }
  .hero-photo {
    position: absolute;
    left: 630px;
    top: 0;
    width: 570px;
    height: 599px;
  }
</style>
</head>
<body>
  <section class="banner">
    <div class="brand">
      <span class="brand-dot"></span>
      <span class="brand-name">Larkvale Powerhouse</span>
    </div>

    <p class="offer offer-title">Group Fitness</p>
    <p class="offer offer-duration">2 Weeks</p>
    <p class="offer offer-headline">UNLIMITED</p>
    <p class="offer offer-detail">group fitness classes</p>
    <p class="offer offer-price">$29</p>
    <p class="offer offer-eligibility">New Clients Only</p>

    <svg class="hero-photo" viewBox="0 0 570 599" role="img" aria-label="Three women in workout clothes doing resistance band exercises on round training platforms">
      <defs>
        <radialGradient id="photoGlow" cx="0.5" cy="0.5" r="0.55">
          <stop offset="0" stop-color="var(--photo-light)" stop-opacity="0.55"/>
          <stop offset="0.6" stop-color="var(--photo-mid)" stop-opacity="0.35"/>
          <stop offset="1" stop-color="var(--photo-mid)" stop-opacity="0"/>
        </radialGradient>
      </defs>
      <ellipse cx="285" cy="300" rx="285" ry="300" fill="url(#photoGlow)"/>
    </svg>
  </section>
</body>
</html>
```